Upmarket Dessert Lounge needs a Business Card Design

We are an upmarket dessert lounge needing a business card to match our image.

We want something that is simple yet beautiful, feminine, classy, sophisticated and elegant. We want it to stand out and don't mind if it is bold.

The design should include our logo and colours of red or maroon with gold highlights. We don't mind if black is used.

Marlow & Quince

Target Market(s)

For those who like to indulge or treat themselves and give in to their temptations on good quality desserts.

Industry/Entity Type

Business

Requirements
Must have
• Must include our logo and our name

Marlow & Quince

M & Q

```html
<!DOCTYPE html>
<html lang="en">
<head>
<meta charset="utf-8">
<title>Marlow &amp; Quince — Business Card</title>
<link href="https://fonts.googleapis.com/css2?family=Cinzel:wght@500&family=Open+Sans:wght@400;600&display=swap" rel="stylesheet">
<style>
  :root {
    --backdrop: #dcd9d5;
    --maroon: #8a1a22;
    --maroon-deep: #5b0c12;
    --gold: #e2b97c;
    --peach: #f2c38d;
    --white: #ffffff;
    --ink-maroon: #7a1820;
  }
  html, body {
    margin: 0;
    padding: 0;
    width: 1200px;
    height: 951px;
    overflow: hidden;
    background: var(--backdrop);
  }
  .canvas {
    position: relative;
    width: 1200px;
    height: 951px;
  }
  .card {
    position: absolute;
    width: 600px;
    height: 343px;
    border-radius: 18px;
    overflow: hidden;
    box-shadow: 0 6px 18px rgba(0,0,0,0.18);
  }
  /* Front */
  .card-front {
    left: 70px;
    top: 110px;
    background: radial-gradient(ellipse at 40% 40%, var(--maroon) 0%, var(--maroon-deep) 100%);
  }
  .corner-ornament {
    position: absolute;
    right: 0;
    top: 0;
    width: 250px;
    height: 110px;
    background: radial-gradient(ellipse at 70% 30%, rgba(226,185,124,0.55) 0%, rgba(226,185,124,0) 70%);
  }
  .front-logo {
    position: absolute;
    left: 40px;
    top: 140px;
    width: 360px;
    text-align: center;
    white-space: nowrap;
    font-family: 'Cinzel', serif;
    font-weight: 500;
    font-size: 30px;
    letter-spacing: 1px;
    color: var(--gold);
  }
  .front-web {
    position: absolute;
    left: 0;
    width: 600px;
    top: 268px;
    text-align: center;
    white-space: nowrap;
    font-family: 'Cinzel', serif;
    font-weight: 500;
    font-size: 17px;
    letter-spacing: 1px;
    color: var(--white);
  }
  /* Back */
  .card-back {
    left: 530px;
    top: 500px;
    background: var(--white);
  }
  .back-shape {
    position: absolute;
    inset: 0;
  }
  .back-heading {
    position: absolute;
    left: 38px;
    top: 30px;
    white-space: nowrap;
    font-family: 'Open Sans', sans-serif;
    font-weight: 600;
    font-size: 23px;
    color: var(--ink-maroon);
  }
  .back-heading .amp { color: var(--peach); }
  .back-logo {
    position: absolute;
    left: 18px;
    top: 172px;
    width: 225px;
    text-align: center;
    white-space: nowrap;
    font-family: 'Cinzel', serif;
    font-weight: 500;
    font-size: 19px;
    color: var(--ink-maroon);
  }
  .back-ornament {
    position: absolute;
    right: 0;
    top: 0;
    width: 200px;
    height: 110px;
    background: radial-gradient(ellipse at 70% 35%, rgba(226,185,124,0.5) 0%, rgba(226,185,124,0) 70%);
  }
  .contact {
    position: absolute;
    left: 348px;
    white-space: nowrap;
    font-family: 'Open Sans', sans-serif;
    font-size: 14px;
    line-height: 19px;
    color: var(--white);
  }
  .contact-address { top: 108px; }
  .contact-lines { top: 218px; }
  .contact-row {
    display: flex;
    align-items: flex-start;
    gap: 8px;
  }
  .contact-row svg {
    width: 13px;
    height: 13px;
    margin-top: 3px;
    flex: none;
    fill: var(--white);
  }
</style>
</head>
<body>
<div class="canvas">

  <section class="card card-front">
    <div class="corner-ornament" role="img" aria-label="Gold floral flourish in the corner"></div>
    <div class="front-logo">MARLOW &amp; QUINCE</div>
    <div class="front-web">www.marlowandquince.com</div>
  </section>

  <section class="card card-back">
    <svg class="back-shape" viewBox="0 0 600 343" width="600" height="343" aria-hidden="true">
      <defs>
        <radialGradient id="backRed" cx="70%" cy="50%" r="70%">
          <stop offset="0" stop-color="#8a1a22"/>
          <stop offset="1" stop-color="#5b0c12"/>
        </radialGradient>
      </defs>
      <path d="M328 0 C 232 70, 236 250, 318 343 L 345 343 C 262 250, 258 80, 352 0 Z" fill="#f2c38d"/>
      <path d="M352 0 C 258 80, 262 250, 345 343 L 600 343 L 600 0 Z" fill="url(#backRed)"/>
    </svg>
    <div class="back-ornament" role="img" aria-label="Gold floral flourish in the corner"></div>
    <div class="back-heading">Marlow <span class="amp">&amp;</span> Quince</div>
    <div class="back-logo">MARLOW &amp; QUINCE</div>

    <div class="contact contact-address">
      <div class="contact-row">
        <svg viewBox="0 0 14 14"><path d="M7 1 L13 7 L11 7 L11 13 L8 13 L8 9 L6 9 L6 13 L3 13 L3 7 L1 7 Z"/></svg>
        <div>4120 Linden Grove Rd.<br>Suite 210-48<br>Halford, TX 78114</div>
      </div>
    </div>

    <div class="contact contact-lines">
      <div class="contact-row">
        <svg viewBox="0 0 14 14"><path d="M3 1 L5.5 1 L6.5 4 L5 5.5 C5.8 7.3 6.7 8.2 8.5 9 L10 7.5 L13 8.5 L13 11 C13 12 12 13 11 13 C6 13 1 8 1 3 C1 2 2 1 3 1 Z"/></svg>
        <div>512-555-0142</div>
      </div>
      <div class="contact-row">
        <svg viewBox="0 0 14 14"><path d="M3 1 H10 V5 H3 Z M1 6 H13 V12 H1 Z M3 8 H11 V9 H3 Z"/></svg>
        <div>512-555-0143</div>
      </div>
      <div class="contact-row">
        <svg viewBox="0 0 14 14"><path d="M1 3 H13 V11 H1 Z M1 3 L7 8 L13 3" fill="none" stroke="#fff" stroke-width="1.5"/></svg>
        <div>info@marlowandquince.com</div>
      </div>
      <div class="contact-row">
        <svg viewBox="0 0 14 14"><circle cx="7" cy="7" r="6"/></svg>
        <div>www.marlowandquince.com</div>
      </div>
    </div>
  </section>

</div>
</body>
</html>
```